We need a complete design for our construction company KELTO CONSTRUCTION based in Auckland New Zealand, we need a logo, website, business card, vehicle design etc..
We are a mid to high-end construction company who work mostly on residential projects and some commercial.

What we want to see in the design;
Professional,
Architectural,
Simple,
Alternative,

We want the design to communicate professionalism, high quality wormanship and and quality service.

Target Market(s)

People looking for a quality building/ construction company

Industry/Entity Type

Construction Company

Contact Information for Business Card

KELTO CONSTRUCTION.co.nz
Lino Verasek
lino@keltoconstruction.example.nz
021 5807 462

Logo Text

KELTO CONSTRUCTION

Number of Pages Required

5+ page

Font styles to use
Sans Serif

Colors

Designer to choose colors to be used in the design.

Requirements
Must have
• Must appear high end, professional, quality, be simple, easy to use, give security to potential clients
Nice to have
• high-quality photos of our recent projects
• about us page
• blog page
• contact us page
• high quality content
Should not have
• should not be hard to use and have too much going on.

```html
<!DOCTYPE html>
<html lang="en">
<head>
<meta charset="utf-8">
<title>Kelto Construction</title>
<link rel="stylesheet" href="https://fonts.googleapis.com/css2?family=Lato:wght@400;700&family=Quicksand:wght@400;500&family=Raleway:wght@400&display=swap">
<style>
:root{
  --gold:#b8913a;
  --ink:#1d1d1d;
  --muted:#8a8a8a;
  --white:#ffffff;
  --footer:#3b3b3b;
  --divider:#e3e3e3;
}
*{margin:0;padding:0;box-sizing:border-box}
html,body{width:918px;height:1200px;overflow:hidden;background:var(--white)}
body{position:relative;font-family:'Lato',sans-serif;color:var(--muted)}
.abs{position:absolute}

.hero{left:0;top:0;width:918px;height:518px;
  background:radial-gradient(ellipse at 50% 40%,#4a5260 0%,#2b3038 45%,#15181d 100%)}
.nav{top:19px;left:0;width:918px;font-size:13px;letter-spacing:.2px}
.nav a{position:absolute;color:#c9c9c9;text-decoration:none}
.nav a.active{color:var(--white);font-weight:700}
.brand{left:0;width:918px;text-align:center;color:var(--gold);font-family:'Quicksand',sans-serif;font-weight:400}
.brand-name{top:150px;font-size:50px;letter-spacing:20px;padding-left:20px}
.brand-sub{top:216px;font-size:19px;letter-spacing:14px;padding-left:14px}
.tagline{top:256px;left:0;width:918px;text-align:center;font-family:'Quicksand',sans-serif;font-weight:500;font-size:27px;color:var(--gold)}
.scroll-cue{left:450px;top:477px}

.about-title{top:553px;left:0;width:918px;text-align:center;font-family:'Quicksand',sans-serif;font-size:29px;color:var(--ink);letter-spacing:.5px}
.about-title span{color:var(--gold)}
.about-text{top:594px;left:90px;width:738px;text-align:center;font-size:11.2px;line-height:17.6px}

.feature{top:660px;width:133px;text-align:center;font-size:12.5px;line-height:14.5px}
.feature svg{display:block;margin:0 auto 14px}
.feature-divider{top:662px;width:1px;height:80px;background:var(--divider)}

.card{top:764px;width:255px;text-align:center}
.card.featured{background:var(--white);box-shadow:0 1px 6px rgba(0,0,0,.16);height:278px}
.card-photo{height:143px}
.card h3{font-family:'Raleway',sans-serif;font-weight:400;font-size:19px;color:var(--gold);margin:15px 0 8px}
.card p{font-size:11.2px;line-height:16px;padding:0 22px}

.footer{left:0;top:1082px;width:918px;height:118px;background:var(--footer)}
.social{top:1113px;left:185px;display:flex;gap:6px}
.social span{width:32px;height:32px;border-radius:50%;border:1.5px solid var(--white)}
.social span.filled{background:var(--white)}
.copyright{top:1160px;left:36px;font-size:11.5px;font-weight:700;color:var(--white)}
.copyright b{color:var(--gold)}
.footer-brand{left:372px;width:176px;text-align:center;color:var(--white);font-family:'Quicksand',sans-serif}
.footer-brand.name{top:1127px;font-size:27px;letter-spacing:10px;padding-left:10px}
.footer-brand.sub{top:1161px;font-size:10.5px;letter-spacing:7px;padding-left:7px}
.contact{left:594px;color:var(--white);font-size:11.5px;line-height:16px}
.contact svg{position:absolute;left:0;top:2px}
.contact p{margin-left:16px}
.contact.phone p{font-weight:700;font-size:13px}
</style>
</head>
<body>

<div class="abs hero" role="img" aria-label="Upward view of tall city towers against a dusky sky"></div>
<nav class="abs nav">
  <a class="active" style="left:243px">HOME</a>
  <a style="left:327px">ABOUT</a>
  <a style="left:417px">PROJECTS</a>
  <a style="left:526px">BLOGS</a>
  <a style="left:612px">CONTACT</a>
</nav>
<div class="abs brand brand-name">KELTO</div>
<div class="abs brand brand-sub">CONSTRUCTION</div>
<h1 class="tagline abs">We Have New Fresh Ideas All The Time</h1>
<svg class="abs scroll-cue" width="18" height="10" viewBox="0 0 18 10"><path d="M1 1l8 8 8-8" fill="none" stroke="#fff" stroke-width="1.2"/></svg>

<h2 class="abs about-title">ABOUT <span>KELTO CONSTRUCTION</span></h2>
<p class="abs about-text">Lorem Ipsum is simply dummy text of the printing and typesetting industry. Lorem Ipsum has been the industry's standard dummy text ever since the 1500s, when an unknown printer took a galley of type and scrambled it to make a type specimen book. It has survived not only five centuries, but also the leap into electronic typesetting, remaining essentially unchanged. It was popularised in the 1960.</p>

<div class="abs feature" style="left:245px">
  <svg width="48" height="42" viewBox="0 0 48 42" fill="none" stroke="#333" stroke-width="1.3">
    <circle cx="24" cy="7" r="4"/><path d="M17 17a7 6 0 0 1 14 0z"/>
    <circle cx="9" cy="24" r="4"/><path d="M2 34a7 6 0 0 1 14 0z"/>
    <circle cx="39" cy="24" r="4"/><path d="M32 34a7 6 0 0 1 14 0z"/>
    <path d="M8 16a18 18 0 0 1 7-8M33 8a18 18 0 0 1 7 8M15 39a18 18 0 0 0 18 0"/>
  </svg>Communicate professionalism</div>
<div class="abs feature-divider" style="left:379px"></div>
<div class="abs feature" style="left:379px">
  <svg width="40" height="42" viewBox="0 0 40 42" fill="#111">
    <rect x="2" y="18" width="7" height="18"/>
    <path d="M12 18l8-14c3 0 4 2 3 6l-2 6h13c2 0 3 2 2 4l-4 15c-1 1-2 1-3 1H12z"/>
  </svg>High quality wormanship</div>
<div class="abs feature-divider" style="left:512px"></div>
<div class="abs feature" style="left:512px">
  <svg width="40" height="42" viewBox="0 0 40 42">
    <circle cx="20" cy="15" r="12" fill="#111"/>
    <path d="M14 15l4 4 8-8" fill="none" stroke="#fff" stroke-width="2"/>
    <path d="M13 25v15l7-6 7 6V25" fill="#111"/>
  </svg>And quality service</div>

<article class="abs card" style="left:59px">
  <div class="card-photo" role="img" aria-label="White layered modern building under blue sky" style="background:linear-gradient(160deg,#2f6fb0,#9ab6cc 70%,#d8dde0)"></div>
  <h3>Project Name</h3>
  <p>Lorem Ipsum is simply dummy text of the printing and typesetting industry. Lorem Ipsum has been the industry.</p>
</article>
<article class="abs card featured" style="left:332px">
  <div class="card-photo" role="img" aria-label="Curved glass terminal building at dusk" style="background:linear-gradient(180deg,#5b86c4,#8fa3b8 55%,#3d4552)"></div>
  <h3>Project Name</h3>
  <p>Lorem Ipsum is simply dummy text of the printing and typesetting industry.</p>
</article>
<article class="abs card" style="left:605px">
  <div class="card-photo" role="img" aria-label="Flowing white curved cultural centre building" style="background:linear-gradient(180deg,#3f7fc0,#b9cfe0 55%,#eef0f2)"></div>
  <h3>Project Name</h3>
  <p>Lorem Ipsum is simply dummy text of the printing and typesetting industry. Lorem Ipsum has been the industry.</p>
</article>

<footer class="abs footer"></footer>
<div class="abs social" aria-label="Social links">
  <span class="filled"></span><span></span><span></span><span></span>
</div>
<p class="abs copyright">© <b>KELTO CONSTRUCTION</b> - 2018. All Rights Reserved.</p>
<div class="abs footer-brand name">KELTO</div>
<div class="abs footer-brand sub">CONSTRUCTION</div>
<div class="abs contact" style="top:1114px">
  <svg width="12" height="16" viewBox="0 0 12 16"><path d="M6 0a6 6 0 0 0-6 6c0 4 6 10 6 10s6-6 6-10a6 6 0 0 0-6-6z" fill="var(--gold)"/><circle cx="6" cy="6" r="2.2" fill="var(--footer)"/></svg>
  <p>123, Lorem ipsum dummy text,<br>Country, 123456.</p>
</div>
<div class="abs contact phone" style="top:1155px">
  <svg width="10" height="14" viewBox="0 0 10 14"><rect x="1" y="1" width="8" height="12" rx="1.5" fill="none" stroke="var(--gold)" stroke-width="1.6"/></svg>
  <p>123 456 7878</p>
</div>

</body>
</html>
```